Boutique custom software development company needs new business card

Our nearly 20 year old custom software development company would like to better include the fact that we are now providing Bitcoin services. These new services are B2B include education (how to acquire and securely hold Bitcoin) and integrating Bitcoin payments into existing ecommerce sites or other existing systems. Please keep the card clean and simple. Attached is our current design and some other files. vextorial.com

Target Market(s)

businesses owners interested in long term relationship

Industry/Entity Type

Custom software development and Bitcoin

Contact Information for Business Card

Dale Parker, dale@vextorial.com, vextorial.com, (888) 555-VXTRL

Font styles to use
Other font styles liked:
• monospace

Requirements
Must have
• double-sided
Nice to have
• clean and simple
Should not have
• physical address

```html
<!DOCTYPE html>
<html lang="en">
<head>
<meta charset="utf-8">
<title>Vextorial business card</title>
<link href="https://fonts.googleapis.com/css2?family=Open+Sans:wght@400;700;800&display=swap" rel="stylesheet">
<style>
  :root {
    --backdrop: #aaaaaa;
    --card: #202024;
    --card-shade: #2d323c;
    --blue: #3b74bc;
    --orange: #f07f22;
    --white: #ffffff;
  }
  * { box-sizing: border-box; margin: 0; padding: 0; }
  html, body { width: 1200px; height: 936px; overflow: hidden; }
  body {
    background: var(--backdrop);
    font-family: "Open Sans", Arial, sans-serif;
    position: relative;
  }
  .card {
    position: absolute;
    width: 780px;
    height: 446px;
    background: var(--card);
    border-radius: 26px;
    overflow: hidden;
    box-shadow: 0 6px 14px rgba(0,0,0,.35);
  }
  .card--back { left: 60px; top: 12px; }
  .card--front { left: 360px; top: 478px; }
  .card__shapes { position: absolute; inset: 0; width: 100%; height: 100%; }

  /* back side */
  .brand-block { position: absolute; right: 60px; top: 60px; display: flex; align-items: center; gap: 26px; }
  .brand-block__square { width: 170px; height: 170px; background: var(--blue); }
  .brand-block__name { color: var(--white); font-weight: 800; font-size: 44px; letter-spacing: 1px; }
  .back-web { position: absolute; right: 40px; bottom: 34px; color: var(--white); font-size: 22px; }

  /* front side */
  .wordmark { position: absolute; left: 48px; top: 62px; color: var(--orange); font-weight: 800; font-size: 56px; letter-spacing: 1px; line-height: 1; }
  .tagline { position: absolute; left: 50px; top: 132px; width: 380px; color: var(--blue); font-size: 20px; line-height: 1.25; }
  .person { position: absolute; right: 50px; top: 200px; font-weight: 800; font-size: 38px; line-height: 1; }
  .person__first { color: var(--orange); }
  .person__last { color: var(--blue); }
  .contact { position: absolute; left: 60px; top: 262px; list-style: none; color: var(--white); font-size: 21px; line-height: 34px; }
  .contact li { display: flex; align-items: center; gap: 12px; }
  .contact svg { width: 20px; height: 20px; fill: var(--orange); flex: none; }
</style>
</head>
<body>

<section class="card card--back" aria-label="Card back">
  <svg class="card__shapes" viewBox="0 0 780 446" aria-hidden="true">
    <polygon points="0,430 520,430 513,446 0,446" fill="var(--blue)"/>
    <polygon points="526,446 552,372 780,372 780,446" fill="var(--orange)"/>
  </svg>
  <div class="brand-block">
    <span class="brand-block__name">Vextorial</span>
    <span class="brand-block__square"></span>
  </div>
  <p class="back-web">www.vextorial.com</p>
</section>

<section class="card card--front" aria-label="Card front">
  <svg class="card__shapes" viewBox="0 0 780 446" aria-hidden="true">
    <rect x="440" y="30" width="300" height="280" fill="var(--card-shade)"/>
    <line x1="90" y1="236" x2="480" y2="236" stroke="var(--blue)" stroke-width="3"/>
    <polygon points="0,424 598,424 590,446 0,446" fill="var(--blue)"/>
    <polygon points="604,446 620,404 780,404 780,446" fill="var(--orange)"/>
  </svg>

  <h1 class="wordmark">VEXTORIAL</h1>
  <p class="tagline">custom applications &amp; Bitcoin services</p>
  <p class="person"><span class="person__first">Dale</span> <span class="person__last">Parker</span></p>

  <ul class="contact">
    <li>
      <svg viewBox="0 0 24 24" aria-hidden="true"><path d="M6.6 10.8a15.1 15.1 0 0 0 6.6 6.6l2.2-2.2c.3-.3.7-.4 1-.2 1.1.4 2.3.6 3.6.6.6 0 1 .4 1 1V20c0 .6-.4 1-1 1A17 17 0 0 1 3 4c0-.6.4-1 1-1h3.5c.6 0 1 .4 1 1 0 1.3.2 2.5.6 3.6.1.3 0 .7-.2 1z"/></svg>
      (888) 555-VXTRL
    </li>
    <li>
      <svg viewBox="0 0 24 24" aria-hidden="true"><path d="M12 2a10 10 0 1 0 0 20 10 10 0 0 0 0-20zm6.9 6h-3a15.7 15.7 0 0 0-1.4-3.6A8 8 0 0 1 18.9 8zM12 4c.8 1.2 1.5 2.5 1.9 4h-3.8c.4-1.5 1.1-2.8 1.9-4zM4.3 14a8.2 8.2 0 0 1 0-4h3.4a16.5 16.5 0 0 0 0 4zm.8 2h3a15.7 15.7 0 0 0 1.4 3.6A8 8 0 0 1 5.1 16zm3-8h-3a8 8 0 0 1 4.4-3.6C8.9 5.5 8.4 6.7 8.1 8zM12 20c-.8-1.2-1.5-2.5-1.9-4h3.8c-.4 1.5-1.1 2.8-1.9 4zm2.3-6H9.7a14.7 14.7 0 0 1 0-4h4.6a14.7 14.7 0 0 1 0 4zm.3 5.6c.6-1.1 1.1-2.3 1.4-3.6h3a8 8 0 0 1-4.4 3.6zm1.7-5.6a16.5 16.5 0 0 0 0-4h3.4a8.2 8.2 0 0 1 0 4z"/></svg>
      www.vextorial.com
    </li>
    <li>
      <svg viewBox="0 0 24 24" aria-hidden="true"><path d="M20 4H4a2 2 0 0 0-2 2v12a2 2 0 0 0 2 2h16a2 2 0 0 0 2-2V6a2 2 0 0 0-2-2zm0 4-8 5-8-5V6l8 5 8-5z"/></svg>
      dale@vextorial.com
    </li>
  </ul>
</section>

</body>
</html>
```